Trendy eye catching business card for lawn mowing business

Turf Tidy, a local community lawn mowing service, requires an eye catching trendy business card to drop into letterboxes.

We could simply throw something together from a Microsoft Word template, but we are wanting something more than this. Some other business’ images are attached for some inspiration.

We are requiring the card to have Turf Tidy with our slogan, Call The Brindles. In addition, provide details with that we are a local, affordable lawn mowing service, and for other gardening matters to simply just ask!
Plus the relevant contact details, phone, email, social media.

Target Market(s)

Local community members who require assistance with their garden care

Industry/Entity Type

Gardening

Contact Information for Business Card

the name TURF TIDY is our logo
telephone logo 0438 215 967
email logo turftidy@postbox-mail.example
Instagram logo turftidy
Facebook logo turftidy.sth
Lawn Mowing Service
Local Affordable
edge trim, blow and clipping removal included.
Other gardening matters, just ask!

Font styles to use
Serif
Sans Serif
Decorative
Script

Colors
9bcb3c
ffffff

Requirements
Must have
• All the details listed in Business Card Details.
Make these words prominent:
Turf Tidy
Lawn Mowing Service
Local
Affordable
Nice to have
• Our slogan ‘Call The Brindles’ incorporated.
Different colour background for front and reverse side
Greens, white and black colours
Subtle grass blades images incorporated
Should not have
• No images of lawnmowers.
No images of men/cartoons.
No using initials for Turf Tidy

```html
<!DOCTYPE html>
<html lang="en">
<head>
<meta charset="utf-8">
<title>Turf Tidy Business Card</title>
<link rel="stylesheet" href="https://fonts.googleapis.com/css2?family=Poppins:wght@400;600;700;800&family=Dancing+Script:wght@600&display=swap">
<style>
  :root{
    --stage:#8f8f8f;
    --mint:#e3ebdc;
    --leaf:#2f8f1f;
    --deep:#0f5a12;
    --forest:#1a7a1c;
    --lime:#6cc935;
    --bright:#9bcb3c;
    --white:#ffffff;
    --ink:#1d4d14;
  }
  *{margin:0;padding:0;box-sizing:border-box}
  html,body{width:1200px;height:801px;overflow:hidden;background:var(--stage)}
  body{font-family:"Poppins",sans-serif;position:relative}
  .card{position:absolute;top:240px;width:520px;height:318px;border-radius:22px;overflow:hidden}
  /* front */
  .card-front{left:45px;background:var(--mint);border-bottom:4px solid var(--lime)}
  .brand{position:absolute;left:28px;top:100px;width:196px;text-align:center}
  .brand-name{font-weight:800;font-size:44px;line-height:1;color:var(--leaf);letter-spacing:1px}
  .brand-slogan{font-family:"Dancing Script",cursive;font-size:25px;color:var(--lime);margin-top:6px;white-space:nowrap}
  .divider{position:absolute;left:238px;top:88px;width:1px;height:140px;background:var(--ink)}
  .contact{position:absolute;left:256px;top:94px;width:246px}
  .contact-name{font-weight:700;font-size:20px;color:var(--deep);margin-bottom:10px;letter-spacing:.5px}
  .contact-list{list-style:none}
  .contact-list li{display:flex;align-items:center;gap:7px;font-size:12px;color:var(--ink);line-height:22px;white-space:nowrap}
  .contact-list svg{width:12px;height:12px;flex:none}
  .dot{width:11px;height:11px;border-radius:50%;border:1.6px solid var(--ink);flex:none}
  /* back */
  .card-back{left:635px;background:radial-gradient(circle at 60% 30%,var(--forest),var(--deep) 80%)}
  .grass{position:absolute;left:0;right:0;bottom:0;height:110px;
    background:linear-gradient(180deg,rgba(108,201,53,0) 0%,rgba(108,201,53,.45) 45%,rgba(155,203,60,.85) 100%)}
  .headline{position:absolute;left:42px;top:36px;width:440px;height:150px;border-radius:28px;
    background:linear-gradient(180deg,#7fd84a,#46ad2a);padding:30px 22px}
  .headline-line{display:flex;align-items:center;gap:10px;font-weight:700;font-size:27px;line-height:1.35;color:var(--deep);letter-spacing:.5px}
  .tick{width:24px;height:24px;flex:none}
  .details{position:absolute;left:0;right:0;top:196px;text-align:center;color:var(--white);font-weight:600;font-size:14px;line-height:1.35}
  .phone-pill{position:absolute;left:120px;top:248px;width:280px;height:44px;border-radius:22px;
    background:linear-gradient(180deg,#fafafa,#bdbdbd);display:flex;align-items:center;gap:10px;padding-left:6px}
  .phone-pill svg{width:34px;height:34px}
  .phone-number{font-weight:800;font-size:28px;color:var(--deep);letter-spacing:1px}
</style>
</head>
<body>
  <section class="card card-front">
    <div class="brand">
      <div class="brand-name">TURF<br>TIDY</div>
      <div class="brand-slogan">Call The Brindles</div>
    </div>
    <div class="divider"></div>
    <div class="contact">
      <div class="contact-name">MILO BRINDLE</div>
      <ul class="contact-list">
        <li><svg viewBox="0 0 24 24"><path fill="#1d4d14" d="M6.6 10.8a15 15 0 0 0 6.6 6.6l2.2-2.2a1 1 0 0 1 1-.25 11 11 0 0 0 3.6.6 1 1 0 0 1 1 1V20a1 1 0 0 1-1 1A17 17 0 0 1 3 4a1 1 0 0 1 1-1h3.5a1 1 0 0 1 1 1c0 1.25.2 2.45.6 3.6a1 1 0 0 1-.25 1z"/></svg>0438 215 967</li>
        <li><svg viewBox="0 0 24 24"><rect x="2" y="5" width="20" height="14" rx="2" fill="#1d4d14"/><path d="M3 6l9 7 9-7" stroke="#e3ebdc" stroke-width="2" fill="none"/></svg>turftidy@postbox-mail.example</li>
        <li><span class="dot"></span>turftidy.example</li>
        <li><span class="dot"></span>turftidy</li>
      </ul>
    </div>
  </section>

  <section class="card card-back">
    <div class="grass" role="img" aria-label="Subtle grass blades along the bottom edge"></div>
    <div class="headline">
      <div class="headline-line"><svg class="tick" viewBox="0 0 24 24"><circle cx="12" cy="12" r="11" fill="#e9f5e1" stroke="#0f5a12" stroke-width="2"/><path d="M7 12.5l3.2 3.2L17 9" stroke="#0f5a12" stroke-width="2.6" fill="none"/></svg>LAWN MOWING SERVICE</div>
      <div class="headline-line"><svg class="tick" viewBox="0 0 24 24"><circle cx="12" cy="12" r="11" fill="#e9f5e1" stroke="#0f5a12" stroke-width="2"/><path d="M7 12.5l3.2 3.2L17 9" stroke="#0f5a12" stroke-width="2.6" fill="none"/></svg>LOCAL. AFFORDABLE.</div>
    </div>
    <p class="details">Edge trim, blow &amp; clipping removal included.<br>Other gardening matters, just ask!</p>
    <div class="phone-pill">
      <svg viewBox="0 0 34 34"><circle cx="17" cy="17" r="16" fill="#2f8f1f"/><circle cx="17" cy="17" r="11" fill="#ffffff"/><path fill="#2f8f1f" d="M13.2 15.2a8 8 0 0 0 5.6 5.6l1.5-1.5a.7.7 0 0 1 .7-.2l2 .5a.7.7 0 0 1 .5.7v1.8a.7.7 0 0 1-.7.7A10.3 10.3 0 0 1 12 12.2a.7.7 0 0 1 .7-.7h1.8a.7.7 0 0 1 .7.5l.5 2a.7.7 0 0 1-.2.7z"/></svg>
      <span class="phone-number">0438 215 967</span>
    </div>
  </section>
</body>
</html>
```